Need Instructors for martial arts school - special flyers to help

We are a kung fu and tai chi martial arts school and we need to appeal to a certain demographic - 16-30, driven, fit, personable - who can join our team of instructors to help grow our school. We envisage this flyer as as roughly between A6 and A7 in size. The kind of thing we can hand to some one we meet and they can easily stick it in a pocket but not so small it gets lost like a business card. We are a professional and serious organisation so don't want to go too dramatic or cheesy to get attention but the design needs to capture the attention of the reader quickly and keep them engaged. Martial arts has quite a bit of material to use for this purpose. NOTE: we are not Karate or Tae Kwon Do - the difference matters. We will upload our current logo and the text we want to use is this for the front:
"Challenge Yourself...
Teaching is the highest form of learning. Be a part of a professional, dedicated team, delivering the highest level Kung Fu...
Copper Wren Martial Arts"
On the back side it should say:
"Seeking martial arts instructors!
We train in one of the world's most effective martial art systems, Choy Li Fut Kung Fu. As an instructor, you will teach both beginner and intermediate level Kung Fu skills to adults and children at Copper Wren Martial Arts, Brisbane's premier martial arts school.
As an instructor, you will:
- Teach fundamentals to children and adults of all ages and abilities
- Progress student's martial arts and life skills
- Deliver fun and engaging classes
- Develop and grow your martial arts skills at an advanced level and pace
In return, you will receive your training tuition, which includes our high level instructor training program, until qualified and then a weekly one one on one with our very own Sifu, as well as one hour training sessions, twice a week , with our team.
At CWMA our motto is "Challenge yourself... for life!"
Contact us on 0491 570 183 to discuss your interest and suitability - ask for Sifu Rory."
There are two fonts we are liking right now for our designs, Merienda One and Red Rose from Google Fonts.
We basically need this to be cool enough to keep someone's attention and not have them throw it away before they have read it.
Info about us on copperwrenexample.com.au

```html
<!DOCTYPE html>
<html lang="en">
<head>
<meta charset="utf-8">
<title>Copper Wren Martial Arts – Instructor Flyer</title>
<link href="https://fonts.googleapis.com/css2?family=Montserrat:wght@500;600;700;800&family=Merienda+One&family=Red+Rose:wght@400&display=swap" rel="stylesheet">
<style>
  :root {
    --red: #e21f2b;
    --red-deep: #b81e27;
    --charcoal: #352f2f;
    --charcoal-soft: #433b3b;
    --paper: #ffffff;
    --light-grey: #ececec;
    --ink: #2a2525;
    --skin-tone: #c79a86;
    --cloth-grey: #7b7b74;
    --lawn: #8fb36a;
  }
  * { box-sizing: border-box; margin: 0; padding: 0; }
  html, body {
    width: 1200px; height: 908px; overflow: hidden;
    background: var(--paper);
    font-family: "Montserrat", Arial, sans-serif;
  }
  .stage { position: relative; width: 1200px; height: 908px; }

  .flyer {
    position: absolute; width: 471px; height: 664px; overflow: hidden;
    box-shadow: 6px 10px 16px rgba(0,0,0,0.18);
  }

  /* Front */
  .flyer--front {
    left: 79px; top: 79px;
    background:
      radial-gradient(ellipse at 0% 100%, rgba(226,31,43,0.85) 0%, rgba(226,31,43,0) 60%),
      linear-gradient(125deg, var(--red) 0%, var(--red-deep) 35%, var(--charcoal) 70%, var(--charcoal) 100%);
  }
  .front__headline {
    position: absolute; left: 72px; top: 20px;
    color: var(--paper); font-weight: 800; font-size: 66px; letter-spacing: -1.5px; line-height: 1;
  }
  .front__subhead {
    position: absolute; left: 168px; top: 94px;
    color: var(--paper); font-weight: 800; font-size: 38px; letter-spacing: -0.5px; line-height: 1;
  }
  .front__photo {
    position: absolute; left: 0; top: 130px; width: 460px; height: 370px;
    background: linear-gradient(160deg, rgba(199,154,134,0.75) 0%, rgba(160,160,155,0.7) 45%, rgba(123,123,116,0.75) 100%);
    clip-path: polygon(25% 0%, 45% 0%, 80% 30%, 100% 97%, 60% 90%, 10% 100%, 0% 90%, 0% 30%);
  }
  .front__pitch {
    position: absolute; right: 31px; top: 286px; width: 260px;
    text-align: right; color: var(--paper);
    font-weight: 600; font-size: 15px; line-height: 22px;
  }
  .front__seal {
    position: absolute; left: 263px; top: 481px; width: 126px; height: 126px;
    border: 1.5px solid var(--paper); border-radius: 50%;
  }
  .front__name {
    position: absolute; left: 0; width: 652px; top: 621px; text-align: center;
    color: var(--paper); font-weight: 800; font-size: 17.5px;
  }

  /* Back */
  .flyer--back { left: 626px; top: 179px; background: var(--red); }
  .back__shapes { position: absolute; inset: 0; }
  .back__title {
    position: absolute; left: 34px; top: 18px;
    font-family: "Merienda One", cursive; color: var(--paper);
    font-size: 33px; line-height: 49px;
  }
  .back__photo {
    position: absolute; border-radius: 50%; border: 3px solid var(--charcoal);
  }
  .back__photo--stretch {
    left: 240px; top: 74px; width: 112px; height: 112px;
    background: linear-gradient(180deg, #e9eef0 0%, #c9c6c2 55%, var(--cloth-grey) 100%);
  }
  .back__photo--park {
    left: 339px; top: 17px; width: 154px; height: 154px;
    background: linear-gradient(180deg, #eef0e8 0%, #f4f4f2 50%, var(--lawn) 100%);
  }
  .back__copy {
    position: absolute; left: 35px; top: 199px; width: 410px;
    color: var(--paper); font-weight: 700; font-size: 13.4px; line-height: 17.7px;
  }
  .back__copy p { margin-bottom: 11px; }
  .duties { list-style: none; margin-bottom: 12px; }
  .duties li { position: relative; padding-left: 21px; margin-bottom: 2px; }
  .duties li::before { content: "-"; position: absolute; left: 0; }
  .back__contact {
    position: absolute; left: 33px; top: 584px; width: 140px;
    color: var(--red); font-weight: 700; font-size: 8.4px; line-height: 11px;
  }
  .back__phone {
    display: block; margin-top: 2px;
    font-size: 19px; font-weight: 800; line-height: 22px; letter-spacing: 0.3px;
  }
  .back__brand {
    position: absolute; left: 199px; top: 577px;
    font-family: "Red Rose", sans-serif; color: var(--ink);
    font-size: 20.5px; line-height: 20px;
  }
  .back__motto {
    display: block; margin-top: 3px;
    font-family: "Merienda One", cursive; color: var(--red); font-size: 11px; line-height: 14px;
  }
  .back__seal {
    position: absolute; left: 357px; top: 568px; width: 80px; height: 80px;
    border: 1.5px solid var(--ink); border-radius: 50%;
  }
</style>
</head>
<body>
<main class="stage">

  <section class="flyer flyer--front" aria-label="Flyer front">
    <h1 class="front__headline">Challenge</h1>
    <div class="front__subhead">Yourself...</div>
    <div class="front__photo" role="img" aria-label="Photo of a kung fu student in a low extended stance"></div>
    <p class="front__pitch">Teaching is the highest form of learning. Be a part of a professional, dedicated team, delivering the highest level Kung Fu...</p>
    <div class="front__seal" aria-hidden="true"></div>
    <div class="front__name">Copper Wren Martial Arts</div>
  </section>

  <section class="flyer flyer--back" aria-label="Flyer back">
    <svg class="back__shapes" width="471" height="664" viewBox="0 0 471 664" aria-hidden="true">
      <polygon points="0,0 471,0 471,138 130,170 108,193 105,167 0,181" fill="var(--charcoal)"/>
      <polygon points="0,581 471,532 471,664 0,664" fill="var(--light-grey)"/>
    </svg>
    <h2 class="back__title">Seeking martial arts<br>instructors!</h2>
    <div class="back__photo back__photo--stretch" role="img" aria-label="Photo of a student stretching in a low lunge"></div>
    <div class="back__photo back__photo--park" role="img" aria-label="Photo of tai chi practitioners in white uniforms in a park"></div>

    <div class="back__copy">
      <p>We train in one of the world's most effective martial art systems, Choy Li Fut Kung Fu. As an instructor, you will teach both beginner and intermediate level Kung Fu skills to adults and children at Copper Wren Martial Arts, Brisbane's premier martial arts school.</p>
      <p style="margin-bottom:2px">As an instructor, you will:</p>
      <ul class="duties">
        <li>Teach fundamentals to children and adults of all ages and abilities</li>
        <li>Progress student's martial arts and life skills</li>
        <li>Deliver fun and engaging classes</li>
        <li>Develop and grow your martial arts skills at an advanced level and pace</li>
      </ul>
      <p>In return, you will receive your training tuition, which includes our high level instructor training program, until qualified and then a weekly one one on one with our very own Sifu, as well as one hour training sessions, twice a week , with our team.</p>
    </div>

    <div class="back__contact">
      To discuss your interest and suitability - ask for Sifu Rory.<br>Contact us on:
      <span class="back__phone">0491 570 183</span>
    </div>
    <div class="back__brand">
      Copper Wren<br>Martial Arts
      <span class="back__motto">"Challenge yourself... for life!</span>
    </div>
    <div class="back__seal" aria-hidden="true"></div>
  </section>

</main>
</body>
</html>
```